Business Card Design Project

Business Card
We are rebranding with a new logo
Industry/Entity Type
Business
Contact Information for Business Card
Dennis Morvale +61 487215963 dennis@quorv.com.au P.O. Box 872 Fernlow QLD 4309
Requirements
Must have
- Logo

```html
<!DOCTYPE html>
<html lang="en">
<head>
<meta charset="utf-8">
<title>Quorv International – Business Card</title>
<link rel="stylesheet" href="https://fonts.googleapis.com/css2?family=Open+Sans:wght@400;600;700&display=swap">
<style>
  :root {
    --backdrop: #2a2a2a;
    --card: #f7f7f7;
    --band-deep: #0a4f73;
    --band-mid: #0e6f9c;
    --band-bright: #1aa0d8;
    --band-shadow: #08425f;
    --brand-blue: #0f6f9f;
    --accent-orange: #ee7a1d;
    --text-grey: #5b5b5b;
    --label-teal: #0f5c82;
    --white: #ffffff;
  }
  * { margin: 0; padding: 0; box-sizing: border-box; }
  html, body {
    width: 1200px;
    height: 915px;
    overflow: hidden;
    background: var(--backdrop);
    font-family: "Open Sans", Arial, sans-serif;
  }
  .business-card {
    position: absolute;
    left: 100px;
    top: 171px;
    width: 1000px;
    height: 572px;
    background: var(--card);
    overflow: hidden;
    box-shadow: 0 12px 40px rgba(0,0,0,0.45);
  }
  .header-band {
    position: absolute;
    inset: 0;
    width: 1000px;
    height: 572px;
  }
  .holder-name {
    position: absolute;
    right: 70px;
    top: 52px;
    color: var(--white);
    font-weight: 700;
    font-size: 28px;
    letter-spacing: 0.2px;
    text-transform: uppercase;
  }
  .brand {
    position: absolute;
    left: 82px;
    top: 300px;
    display: flex;
    align-items: center;
    gap: 16px;
  }
  .brand-dot {
    width: 34px;
    height: 34px;
    border-radius: 50%;
    background: var(--accent-orange);
  }
  .brand-name {
    color: var(--brand-blue);
    font-weight: 600;
    font-size: 44px;
    line-height: 1;
  }
  .contact {
    position: absolute;
    left: 84px;
    top: 420px;
    color: var(--text-grey);
    font-size: 21px;
    line-height: 1.65;
  }
  .contact-label {
    color: var(--label-teal);
    font-weight: 700;
  }
  .contact-item { margin-right: 14px; }
</style>
</head>
<body>
  <main class="business-card">
    <svg class="header-band" viewBox="0 0 1000 572" aria-hidden="true">
      <defs>
        <linearGradient id="bandGradient" x1="0" y1="0" x2="1" y2="0.4">
          <stop offset="0" stop-color="var(--band-deep)"/>
          <stop offset="0.55" stop-color="var(--band-bright)"/>
          <stop offset="1" stop-color="var(--band-mid)"/>
        </linearGradient>
      </defs>
      <path d="M0,0 H1000 V300 C800,150 450,95 0,108 Z" fill="var(--band-shadow)"/>
      <path d="M0,0 H1000 V270 C780,130 430,78 0,92 Z" fill="url(#bandGradient)"/>
    </svg>

    <h1 class="holder-name">Dennis Morvale</h1>

    <div class="brand">
      <span class="brand-dot"></span>
      <span class="brand-name">Quorv International</span>
    </div>

    <address class="contact" style="font-style: normal;">
      <div>P.O. Box 872 Fernlow QLD 4309</div>
      <div>
        <span class="contact-item"><span class="contact-label">P:</span> +61 487215963</span>
        <span class="contact-item"><span class="contact-label">E:</span> dennis@quorv.com.au</span>
        <span class="contact-item"><span class="contact-label">W:</span> www.quorv.com.au</span>
      </div>
    </address>
  </main>
</body>
</html>
```